we need an experienced designer to design the tube for our toothpaste

Design guidelines:
1. On the front side, our product logo (‘K7320’) should be prominent enough.
2. Our brand logo (‘lumbrisk’) could be small-size and it's just a trademark indeed.

Some information here for your reference:
1. The color of toothpaste cap is white.
2. We hope that the primary color in the design is blue.
3.‘F’ in ‘K7320’ stands for ‘lumbrisk’ and ‘fluoride’.
4. We will use aluminum-plastic composite materials to make toothpaste tubes. In addition to the design, we also hope that you can make relevant suggestions on the special requirements of printing.

At last, we hope that you could submit both 2D design and 3D visual effects.

Attachments:
Product logo: K7320
Brand logo: lumbrisk
illustration ONE: metal braces
illustration TWO: clear aligners

Colors
0094D4
00A9DD
6FCCEA
C7EBF8
E9F6FB

Requirements
Must have
• as attached

```html
<!DOCTYPE html>
<html lang="en">
<head>
<meta charset="utf-8">
<title>K7320 Orthodontic Toothpaste – Tube Label Layout</title>
<link href="https://fonts.googleapis.com/css2?family=Fira+Sans+Condensed:ital,wght@0,400;0,500;0,700;0,800;1,400;1,700;1,800&family=Montserrat:wght@400;500&display=swap" rel="stylesheet">
<style>
  :root {
    --tube-blue: #0474b8;
    --ink-blue: #0b6db3;
    --white: #ffffff;
    --frame: #2a2226;
    --guide-red: #e0282e;
    --dim-ink: #231f20;
    --silver-dark: #9c9c9c;
    --silver-light: #e6e6e6;
    --gum-pink: #f3c4bb;
    --gum-red: #e2737a;
  }
  html, body {
    margin: 0;
    padding: 0;
    width: 1200px;
    height: 960px;
    overflow: hidden;
    background: var(--white);
  }
  .sheet { display: block; width: 1200px; height: 960px; }
  .label-frame { fill: none; stroke: var(--frame); stroke-width: 3; }
  .panel-line { stroke: var(--frame); stroke-width: 1.2; opacity: .55; }
  .blue-field { fill: var(--tube-blue); }
  .white-field { fill: var(--white); }
  .guide { stroke: var(--guide-red); stroke-width: 2; stroke-dasharray: 7 7; fill: none; }
  .dim-label { font-family: "Montserrat", sans-serif; fill: var(--dim-ink); }
  .front-title { font-family: "Fira Sans Condensed", sans-serif; font-style: italic; font-weight: 800; fill: var(--ink-blue); text-anchor: middle; }
  .flavour { font-family: "Fira Sans Condensed", sans-serif; font-weight: 400; fill: var(--ink-blue); text-anchor: middle; }
  .back-title { font-family: "Fira Sans Condensed", sans-serif; font-weight: 500; fill: var(--ink-blue); text-anchor: middle; font-size: 37px; }
  .on-blue { font-family: "Fira Sans Condensed", sans-serif; fill: var(--white); }
  .product-mark { font-weight: 800; font-size: 190px; letter-spacing: -4px; }
  .brand-mark { font-weight: 700; font-size: 44px; }
  .claim { font-style: italic; font-size: 27px; }
  .benefits { font-size: 29px; letter-spacing: .5px; }
  .copy { font-size: 18.5px; }
  .net-wt { font-size: 14px; }
</style>
</head>
<body>
<svg class="sheet" viewBox="940 60 1100 880" preserveAspectRatio="xMidYMid meet" xmlns="http://www.w3.org/2000/svg" role="img" aria-label="K7320 toothpaste tube label flat layout with dimensions">
  <defs>
    <linearGradient id="silverBand" x1="0" y1="0" x2="0" y2="1">
      <stop offset="0" stop-color="var(--silver-dark)"/>
      <stop offset="1" stop-color="var(--silver-light)"/>
    </linearGradient>
  </defs>

  <g transform="translate(1040 130) scale(0.5) translate(-1040 -60)">
    <!-- dimension guides -->
    <g class="dimensions">
      <text class="dim-label" x="1750" y="110" font-size="28" text-anchor="middle">3*8mm</text>
      <line class="guide" x1="995" y1="153" x2="1095" y2="153"/>
      <line class="guide" x1="995" y1="280" x2="1095" y2="280"/>
      <line class="guide" x1="995" y1="1453" x2="1095" y2="1453"/>
      <line class="guide" x1="995" y1="1500" x2="1095" y2="1500"/>
      <line class="guide" x1="1062" y1="153" x2="1062" y2="1500"/>
      <text class="dim-label" font-size="30" transform="translate(1042 268) rotate(-90)">14mm</text>
      <text class="dim-label" font-size="30" transform="translate(1042 1500) rotate(-90)">5mm</text>
      <text class="dim-label" font-size="92" text-anchor="middle" transform="translate(1012 805) rotate(-90)">147.638mm</text>

      <line class="guide" x1="1108" y1="1505" x2="1108" y2="1640"/>
      <line class="guide" x1="1117" y1="1505" x2="1117" y2="1640"/>
      <line class="guide" x1="1975" y1="1505" x2="1975" y2="1640"/>
      <line class="guide" x1="1993" y1="1505" x2="1993" y2="1640"/>
      <line class="guide" x1="1117" y1="1538" x2="1975" y2="1538"/>
      <text class="dim-label" font-size="92" x="1545" y="1635" text-anchor="middle">97mm</text>
      <text class="dim-label" font-size="30" transform="translate(1148 1615) rotate(-90)">1mm</text>
      <text class="dim-label" font-size="30" transform="translate(1972 1622) rotate(-90)">2mm</text>
    </g>

    <!-- label artwork -->
    <g class="label">
      <rect class="white-field" x="1108" y="153" width="885" height="1347"/>
      <rect class="blue-field" x="1108" y="573" width="885" height="927"/>
      <rect x="1108" y="563" width="55" height="12" fill="url(#silverBand)"/>
      <rect x="1587" y="563" width="406" height="12" fill="url(#silverBand)"/>
      <path class="white-field" d="M1163 563 Q1380 740 1587 563 L1587 560 L1163 560 Z"/>
      <path d="M1163 566 Q1380 735 1587 566" fill="none" stroke="url(#silverBand)" stroke-width="14"/>

      <line class="panel-line" x1="1163" y1="162" x2="1163" y2="1497"/>
      <line class="panel-line" x1="1587" y1="162" x2="1587" y2="1497"/>
      <rect class="label-frame" x="1108" y="153" width="885" height="1347"/>
      <polyline fill="none" stroke="var(--frame)" stroke-width="2.5" points="1117,1497 1117,162 1975,162 1975,1497"/>

      <!-- front panel -->
      <g class="front-panel">
        <text class="front-title" x="1375" y="377" font-size="72">Fluoride</text>
        <text class="front-title" x="1375" y="452" font-size="74">1450 ppm</text>
        <text class="flavour" x="1381" y="525" font-size="38">Double Mint</text>

        <text class="on-blue net-wt" transform="translate(1553 700) rotate(-90)">NET WT. 85g</text>
        <text class="on-blue product-mark" transform="translate(1440 1412) rotate(-90)">K7320</text>
        <g transform="translate(1294 1410) rotate(-90)">
          <text class="on-blue brand-mark" x="0" y="0">lumbrisk</text>
          <circle cx="172" cy="-14" r="7" fill="var(--white)"/>
        </g>
        <text class="on-blue claim" transform="translate(1486 1410) rotate(-90)">ORTHODONTIC TOOTHPASTE</text>
        <text class="on-blue claim" transform="translate(1527 1410) rotate(-90)">ENHANCED CAVITY PREVENTION AND GUM PROTECTION</text>
        <text class="on-blue claim" transform="translate(1558 1410) rotate(-90)">FOR USE WHEN WEARING METAL BRACES AND CLEAR ALIGNERS</text>
      </g>

      <!-- back panel -->
      <g class="back-panel">
        <text class="back-title" x="1780" y="342">PREMIUM ORAL CARE</text>
        <text class="back-title" x="1780" y="377">DURING ORTHODONTIC</text>
        <text class="back-title" x="1780" y="412">TREATMENT</text>
        <rect x="1620" y="443" width="155" height="92" fill="var(--gum-pink)" role="img" aria-label="Illustration of teeth with clear aligners"/>
        <rect x="1787" y="443" width="155" height="92" fill="var(--gum-pink)" role="img" aria-label="Illustration of teeth with metal braces"/>

        <text class="on-blue benefits" transform="translate(1656 1410) rotate(-90)">● PREVENT CAVITY   ● FRESHEN BREATH   ● STRENGTHEN TEETH</text>
        <text class="on-blue copy" transform="translate(1700 1410) rotate(-90)">Directions</text>
        <text class="on-blue copy" transform="translate(1724 1410) rotate(-90)">Apply at least one inch strip of the product onto a soft bristle toothbrush. Brush teeth thoroughly, for at least</text>
        <text class="on-blue copy" transform="translate(1748 1410) rotate(-90)">three minutes twice a day.</text>
        <text class="on-blue copy" transform="translate(1787 1410) rotate(-90)">Ingredients:</text>
        <text class="on-blue copy" transform="translate(1811 1410) rotate(-90)">Aqua, Sorbitol, Hydrated Silica, Glycerin, PEG-12, Sodium Lauryl Sulfate, Aroma, Cellulose Gum, Titanium</text>
        <text class="on-blue copy" transform="translate(1835 1410) rotate(-90)">Dioxide, Potassium Sorbate, Allantoin, Sodium Fluoride, Citric Acid, Peppermint Essence, Sodium Saccharin,</text>
        <text class="on-blue copy" transform="translate(1859 1410) rotate(-90)">CI 47005, CI 42090, Cinnamal.</text>
        <text class="on-blue copy" transform="translate(1897 1410) rotate(-90)">Warnings:</text>
        <text class="on-blue copy" transform="translate(1921 1410) rotate(-90)">Do not ingest. Keep out of reach of children under 6 years of age.</text>
      </g>
    </g>
  </g>
</svg>
</body>
</html>
```